Larkspur Talent IT Recruiting firm needs a business card design for Recruiters, Sourcers, and Account

We need business cards that allow us to change all contact info, names, titles (Recruiter, Sourcer, Account Manager, Director, CEO, etc) per person since we have three offices, in three cities, Phoenix, Austin, and Las Vegas. We do recruiting and contractors for IT positions (Developers, Architects, Software Engineers, Security Engineers, Help Desk, DBAs, PMs, Scrum Masters, etc.) Our client companies are very diverse from Meridian 100 to silicone Valley type start-ups.

So, while we what hip, techie, and quirky, it still needs to be professional. Primary color we use is blue, with silver as a secondary color.

Target Market(s)

IT, Technology

Industry/Entity Type

Business

Contact Information for Business Card

Company name: Larkspur Talent, Inc.
Website: www.larkspurtalent.example
Logos for Careerloop, Blipster, and Myriada

Name, Title, Office Number, Cell Number, email

Font styles to use
Serif
Sans Serif

Colors
0455a3
d5d5d5

Requirements
Nice to have
• The grey I selected below is not necessary - but, would like silver included. I included a card design (File 3: LTI early trial example.jpg) that I had started on. It's very rough, and not quite what we're looking for, but what we did like is the logo, big, maybe a bit faded, off center, goes out of frame, etc. Still looking for other ideas - you are the pros! But, just an idea of a design element we liked.

```html
<!DOCTYPE html>
<html lang="en">
<head>
<meta charset="utf-8">
<title>Larkspur Talent — Business Card</title>
<link rel="stylesheet" href="https://fonts.googleapis.com/css2?family=Open+Sans:wght@400;600;700&family=Marcellus+SC&display=swap">
<style>
  :root {
    --blue: #0f6fb3;
    --blue-light: #2aa6dc;
    --ink: #3a3a3a;
    --ink-soft: #6b6b6b;
    --silver-top: #f4f4f4;
    --silver-bottom: #d5d5d5;
    --paper: #fbfbfb;
    --band: #2b2b2b;
    --stage: #ecebe8;
    --icon: #555555;
  }
  * { box-sizing: border-box; margin: 0; padding: 0; }
  html, body { width: 1200px; height: 1023px; overflow: hidden; }
  body {
    background: var(--stage);
    font-family: "Open Sans", Arial, sans-serif;
    position: relative;
  }
  .card {
    position: absolute;
    left: 250px;
    width: 700px;
    height: 400px;
    border-radius: 4px;
    overflow: hidden;
    box-shadow: 0 10px 28px rgba(0,0,0,.18);
  }
  /* ---------- front ---------- */
  .card--front { top: 70px; background: var(--paper); }
  .front__upper {
    position: absolute; inset: 0 0 170px 0;
    background: linear-gradient(180deg, var(--silver-top), var(--silver-bottom));
  }
  .front__rule {
    position: absolute; left: 0; right: 0; top: 230px; height: 6px;
    background: var(--band);
  }
  .brand { display: flex; align-items: center; gap: 14px; }
  .brand__name {
    font-family: "Open Sans", Arial, sans-serif;
    font-weight: 400; color: var(--ink);
    letter-spacing: 3px;
    white-space: nowrap;
  }
  .brand__dot {
    flex: none;
    border-radius: 50%;
    background: radial-gradient(circle at 40% 35%, var(--blue-light), var(--blue));
  }
  .front__brand { position: absolute; left: 0; right: 0; top: 38px; justify-content: center; }
  .front__brand .brand__name { font-size: 34px; }
  .front__brand .brand__dot { width: 34px; height: 34px; }
  .tagline {
    font-family: "Marcellus SC", Georgia, serif;
    color: var(--ink-soft); letter-spacing: 4px;
    white-space: nowrap;
  }
  .front__tagline { position: absolute; top: 96px; left: 0; right: 0; text-align: center; font-size: 14px; }
  .front__company {
    position: absolute; top: 126px; left: 0; right: 0; text-align: center;
    font-weight: 700; font-size: 24px; color: var(--ink); letter-spacing: .5px;
  }
  .front__person {
    position: absolute; top: 160px; left: 0; right: 0; text-align: center;
    font-weight: 600; font-size: 26px; color: var(--blue);
  }
  .front__title {
    position: absolute; top: 196px; left: 0; right: 0; text-align: center;
    font-size: 13px; color: var(--ink-soft);
  }
  .contacts { position: absolute; top: 272px; list-style: none; }
  .contacts li {
    display: flex; align-items: center; gap: 10px;
    font-size: 15px; color: var(--blue); line-height: 30px;
    white-space: nowrap;
  }
  .contacts svg { width: 18px; height: 18px; flex: none; }
  .contacts--left { left: 40px; }
  .contacts--right { right: 34px; }
  .front__mark {
    position: absolute; left: 310px; top: 236px; width: 80px; height: 164px;
  }
  /* ---------- back ---------- */
  .card--back {
    top: 540px;
    background: linear-gradient(180deg, var(--silver-top), var(--silver-bottom));
  }
  .back__band {
    position: absolute; left: 0; top: 0; bottom: 0; width: 130px;
    background: var(--band);
    display: flex; align-items: center; justify-content: center;
  }
  .back__band span {
    writing-mode: vertical-rl; transform: rotate(180deg);
    font-weight: 700; font-size: 30px; letter-spacing: 1px; color: var(--blue);
    white-space: nowrap;
  }
  .back__brand { position: absolute; left: 130px; right: 0; top: 140px; justify-content: center; }
  .back__brand .brand__name { font-size: 44px; }
  .back__brand .brand__dot { width: 48px; height: 48px; }
  .back__tagline { position: absolute; left: 130px; right: 0; top: 218px; text-align: center; font-size: 18px; }
</style>
</head>
<body>

<section class="card card--front" aria-label="Card front">
  <div class="front__upper"></div>
  <div class="front__rule"></div>

  <div class="brand front__brand">
    <span class="brand__dot"></span>
    <span class="brand__name">LARKSPUR TALENT</span>
  </div>
  <p class="tagline front__tagline">BUILDING THE BEST TEAMS</p>
  <p class="front__company">LARKSPUR TALENT, INC</p>
  <p class="front__person">Dana Whitfield</p>
  <p class="front__title">Manager</p>

  <ul class="contacts contacts--left">
    <li>
      <svg viewBox="0 0 18 18"><rect width="18" height="18" rx="2" fill="var(--icon)"/><path d="M5 4h2.5l1 3-1.5 1a7 7 0 0 0 3 3l1-1.5 3 1V13a1 1 0 0 1-1 1A9 9 0 0 1 4 5a1 1 0 0 1 1-1z" fill="#fff"/></svg>
      00 4821-6093
    </li>
    <li>
      <svg viewBox="0 0 18 18"><rect width="18" height="18" rx="2" fill="var(--icon)"/><rect x="6" y="3.5" width="6" height="11" rx="1" fill="#fff"/><rect x="7" y="5" width="4" height="7" fill="var(--icon)"/></svg>
      03 517 284 640
    </li>
    <li>
      <svg viewBox="0 0 18 18"><rect width="18" height="18" rx="2" fill="var(--icon)"/></svg>
      www.blipster.example
    </li>
  </ul>

  <svg class="front__mark" viewBox="0 0 80 164" aria-hidden="true">
    <line x1="40" y1="0" x2="40" y2="164" stroke="var(--band)" stroke-width="1.5"/>
    <defs>
      <radialGradient id="markFill" cx="40%" cy="35%" r="70%">
        <stop offset="0" stop-color="#2aa6dc"/>
        <stop offset="1" stop-color="#0f6fb3"/>
      </radialGradient>
    </defs>
    <circle cx="40" cy="64" r="36" fill="url(#markFill)"/>
  </svg>

  <ul class="contacts contacts--right">
    <li>
      <svg viewBox="0 0 18 18"><rect width="18" height="18" rx="2" fill="var(--icon)"/></svg>
      www.myriada.example
    </li>
    <li>
      <svg viewBox="0 0 18 18"><rect width="18" height="18" rx="2" fill="var(--icon)"/><rect x="3.5" y="5" width="11" height="8" fill="#fff"/><path d="M3.5 5l5.5 4.5L14.5 5" fill="none" stroke="var(--icon)" stroke-width="1.2"/></svg>
      dana.whitfield@mailbox.example
    </li>
    <li>
      <svg viewBox="0 0 18 18"><rect width="18" height="18" rx="2" fill="var(--icon)"/><circle cx="9" cy="9" r="5" fill="none" stroke="#fff" stroke-width="1.2"/><path d="M4 9h10M9 4c-3 3-3 7 0 10M9 4c3 3 3 7 0 10" fill="none" stroke="#fff" stroke-width="1"/></svg>
      www.larkspurtalent.example
    </li>
  </ul>
</section>

<section class="card card--back" aria-label="Card back">
  <div class="back__band"><span>LARKSPUR TALENT, INC</span></div>
  <div class="brand back__brand">
    <span class="brand__dot"></span>
    <span class="brand__name">LARKSPUR TALENT</span>
  </div>
  <p class="tagline back__tagline">BUILDING THE BEST TEAMS</p>
</section>

</body>
</html>
```